Business Card for a Dental Office

The design should communicate integrity, quality and reliability. We also want the card look elegant, simple, but still stand out, different from the traditional-dental-office business card.

Industry/Entity Type

Business

```html
<!DOCTYPE html>
<html lang="en">
<head>
<meta charset="utf-8">
<title>Harbour Dental Centre – Business Card</title>
<link rel="stylesheet" href="https://fonts.googleapis.com/css2?family=Open+Sans:wght@400;500;600;700&display=swap">
<style>
  :root {
    --page-bg: #e9e6e1;
    --card-bg: #ffffff;
    --ink: #111111;
    --text: #1e1e1e;
    --gold: #b39a1a;
    --gold-light: #f3e32a;
    --gold-dark: #b59f10;
    --rule: #1a1a1a;
  }
  * { box-sizing: border-box; margin: 0; padding: 0; }
  html, body {
    width: 1200px; height: 1000px; overflow: hidden;
    background: var(--page-bg);
    font-family: "Open Sans", Arial, sans-serif;
    color: var(--text);
  }
  .canvas { position: relative; width: 1200px; height: 1000px; }
  .card {
    position: absolute; left: 265px; width: 666px; height: 397px;
    background: var(--card-bg);
    box-shadow: 0 4px 14px rgba(0,0,0,.25);
    overflow: hidden;
  }
  .card--top { top: 73px; }
  .card--bottom { top: 532px; }

  .brand { position: absolute; left: 33px; top: 62px; display: flex; align-items: center; gap: 14px; }
  .brand__mark { width: 62px; height: 62px; background: var(--ink); flex: none; }
  .brand__text { display: flex; flex-direction: column; }
  .brand__name {
    font-size: 26px; font-weight: 700;
    color: var(--ink); line-height: 32px; white-space: nowrap;
  }
  .brand__tagline {
    font-size: 13px; font-weight: 500;
    color: var(--gold); letter-spacing: 0.8px; margin-top: 2px; white-space: nowrap;
  }

  .person { position: absolute; left: 33px; top: 203px; width: 600px; }
  .person__name { font-size: 20px; font-weight: 600; color: var(--ink); line-height: 26px; }
  .person__role { display: flex; align-items: flex-end; gap: 10px; font-size: 15px; line-height: 20px; }
  .person__rule { flex: 1; height: 1.5px; background: var(--rule); margin-bottom: 5px; }

  .contacts { position: absolute; left: 33px; top: 275px; list-style: none; }
  .contacts li { display: flex; align-items: center; gap: 6px; font-size: 15px; line-height: 23px; }
  .contacts svg { width: 16px; height: 12px; fill: var(--gold); }

  .address {
    position: absolute; right: 33px; top: 297px;
    font-style: normal; text-align: right; font-size: 15px; line-height: 24px;
  }

  .band { position: absolute; left: 0; bottom: 0; width: 100%; height: 32px; display: flex; }
  .band__gold { width: 305px; background: linear-gradient(90deg, var(--gold-dark) 0%, var(--gold-light) 60%, var(--gold-dark) 100%); }
  .band__black { flex: 1; background: var(--ink); }
</style>
</head>
<body>
<main class="canvas">
  <section class="card card--top" aria-label="Business card">
    <div class="brand">
      <span class="brand__mark"></span>
      <div class="brand__text">
        <span class="brand__name">HARBOUR DENTAL CENTRE</span>
        <span class="brand__tagline">CARING FOR EVERY SMILE, EVERY DAY</span>
      </div>
    </div>
    <div class="person">
      <p class="person__name">Daniel Reyes, PHA</p>
      <p class="person__role"><span>President</span><span class="person__rule"></span></p>
    </div>
    <ul class="contacts">
      <li><svg viewBox="0 0 16 12"><path d="M1 4c0-2 3-3 7-3s7 1 7 3v1h-4V4H5v1H1zM4 6h8l2 5H2z"/></svg>+ 000 000 0000</li>
      <li><svg viewBox="0 0 16 12"><path d="M4 0h8v3H4zM1 4h14v5h-3v3H4V9H1zM5 8v3h6V8z"/></svg>+ 000 000 0000</li>
      <li><svg viewBox="0 0 16 12"><path d="M0 0h16v1L8 6 0 1zM0 3l8 5 8-5v9H0z"/></svg>info@harbourdentalcare.com</li>
    </ul>
    <address class="address">Level 12, 48 Meridian House<br>Sydney, New South Wales</address>
    <div class="band"><span class="band__gold"></span><span class="band__black"></span></div>
  </section>

  <section class="card card--bottom" aria-label="Business card">
    <div class="brand">
      <span class="brand__mark"></span>
      <div class="brand__text">
        <span class="brand__name">HARBOUR DENTAL CENTRE</span>
        <span class="brand__tagline">CARING FOR EVERY SMILE, EVERY DAY</span>
      </div>
    </div>
    <div class="person">
      <p class="person__name">Daniel Reyes, PHA</p>
      <p class="person__role"><span>President</span><span class="person__rule"></span></p>
    </div>
    <ul class="contacts">
      <li><svg viewBox="0 0 16 12"><path d="M1 4c0-2 3-3 7-3s7 1 7 3v1h-4V4H5v1H1zM4 6h8l2 5H2z"/></svg>+ 000 000 0000</li>
      <li><svg viewBox="0 0 16 12"><path d="M4 0h8v3H4zM1 4h14v5h-3v3H4V9H1zM5 8v3h6V8z"/></svg>+ 000 000 0000</li>
      <li><svg viewBox="0 0 16 12"><path d="M0 0h16v1L8 6 0 1zM0 3l8 5 8-5v9H0z"/></svg>info@harbourdentalcare.com</li>
    </ul>
    <address class="address">Level 12, 48 Meridian House<br>Sydney, New South Wales</address>
    <div class="band"><span class="band__gold"></span><span class="band__black"></span></div>
  </section>
</main>
</body>
</html>
```